Yacht, Boats, Watersports company needs a redesign of business card

Hello Designers!
We are a Boat dealership company that sells fun in the water, we sell boats, Yachts, Kayaks and also yacht WaterSport toys. We are looking to redesign our business cards in to something a little bit more sophisticated. in a way that we can make better use of our company colors. I'm attaching a zipped file containing the company 3 sets of company logo which one is an horizontal another one is a vertical and also a chromed 3d logo. Also is included two set of business cards that we use and also some designs that i think it's interesting. We use PMS 2026c Orange and PMS 7687C Blue. I would like to see at least two different options with the orange as accent and also using blue as an accent color. It's really important for the business cards to have a font option and size that is legible to most people. Our current website is wwww.coralpennant.com. Please visit if you want to have a better feeling of the Boat dealership
You can send Single sided or double side options. We are now using single sided but we may be open for a double side option if we really like the design.
Target Market(s)
Marine, boat sales, yacht sales, water toys sales/
Contact Information for Business Card
Name: Dale Whitcombe
Address: 212 North Fenwick Lane,
Marlin Cove, FL 33190
Phone: 954-731-8842
Fax: 954:731-8843
Cell: 954-382-1490
Email: dw@coralpennant.com
Website: coralpennant.com
Requirements
Must have
- the current information of the business card provided.
logo
use the PMS Colors
Nice to have
- a touch of elegance and sophistication but simple
Should not have
- should not have any typography that is hard to read, the card should be simple but yet sophisticated.

```html
<!DOCTYPE html>
<html lang="en">
<head>
<meta charset="utf-8">
<title>Coral Pennant — Business Card</title>
<link href="https://fonts.googleapis.com/css2?family=Montserrat:wght@400;500;800&display=swap" rel="stylesheet">
<style>
  :root {
    --backdrop: #1a1a1c;
    --card: #2c2c2e;
    --orange: #f05a22;
    --blue: #1d4e8f;
    --blue-bright: #2f7fd8;
    --ink: #f2f2f2;
  }
  * { margin: 0; padding: 0; box-sizing: border-box; }
  html, body { width: 1200px; height: 786px; overflow: hidden; }
  body {
    background: var(--backdrop);
    font-family: "Montserrat", sans-serif;
    position: relative;
  }
  .card {
    position: absolute;
    top: 238px;
    width: 540px;
    height: 310px;
    background: var(--card);
    box-shadow: 0 18px 40px rgba(0,0,0,.55);
    overflow: hidden;
  }
  .card--details { left: 40px; }
  .card--brand { left: 620px; }

  .edge-bands { position: absolute; left: 0; bottom: 0; width: 540px; height: 14px; }

  .brand {
    position: absolute;
    display: flex;
    align-items: center;
    gap: 12px;
  }
  .brand__mark { border-radius: 50%; flex: none; }
  .brand__name {
    font-weight: 800;
    letter-spacing: .1em;
    text-transform: uppercase;
    white-space: nowrap;
  }
  .card--details .brand { left: 30px; top: 136px; gap: 10px; }
  .card--details .brand__mark { width: 32px; height: 32px; border: 3px solid var(--orange); }
  .card--details .brand__name { font-size: 15px; color: var(--blue-bright); }

  .divider {
    position: absolute;
    left: 262px; top: 52px;
    width: 1.5px; height: 170px;
    background: var(--orange);
  }

  .contact { position: absolute; left: 284px; top: 50px; color: var(--ink); }
  .contact__name {
    font-weight: 800;
    font-size: 20px;
    letter-spacing: .05em;
    color: var(--orange);
    text-transform: uppercase;
    margin-bottom: 6px;
    white-space: nowrap;
  }
  .contact__address { font-size: 11.5px; line-height: 1.45; margin-bottom: 3px; }
  .contact__list { list-style: none; font-size: 11.5px; line-height: 1.6; }
  .contact__list li { display: flex; align-items: center; gap: 7px; }
  .contact__list svg { width: 10px; height: 10px; flex: none; }
  .contact__web-domain { color: var(--orange); }

  .card--brand .brand { left: 50%; top: 50%; transform: translate(-50%, -60%); gap: 16px; }
  .card--brand .brand__mark { width: 54px; height: 54px; border: 4px solid var(--orange); }
  .card--brand .brand__name { font-size: 28px; color: var(--blue-bright); }
</style>
</head>
<body>

<section class="card card--details">
  <div class="brand">
    <span class="brand__mark"></span>
    <span class="brand__name">Coral Pennant</span>
  </div>

  <div class="divider"></div>

  <div class="contact">
    <p class="contact__name">Dale Whitcombe</p>
    <p class="contact__address">212 North Fenwick Lane,<br>Marlin Cove, FL 33190</p>
    <ul class="contact__list">
      <li>
        <svg viewBox="0 0 10 10"><path d="M2 1l2 2-1 1.2c.6 1.2 1.5 2.1 2.8 2.8L7 6l2 2-1.2 1.4C4.5 9 1 5.5.6 2.2z" fill="var(--orange)"/></svg>
        <span>954-731-8842</span>
      </li>
      <li>
        <svg viewBox="0 0 10 10"><rect x="1" y="4" width="8" height="5" rx="1" fill="var(--orange)"/><rect x="3" y="1" width="4" height="3" fill="var(--orange)"/></svg>
        <span>954:731-8843</span>
      </li>
      <li>
        <svg viewBox="0 0 10 10"><rect x="2.5" y=".8" width="5" height="8.4" rx="1" fill="none" stroke="var(--orange)" stroke-width="1.2"/></svg>
        <span>954-382-1490</span>
      </li>
      <li>
        <svg viewBox="0 0 10 10"><rect x=".8" y="2" width="8.4" height="6" fill="none" stroke="var(--orange)" stroke-width="1.1"/><path d="M1 2.5l4 3 4-3" fill="none" stroke="var(--orange)" stroke-width="1.1"/></svg>
        <span>dw@coralpennant.com</span>
      </li>
      <li>
        <svg viewBox="0 0 10 10"><circle cx="5" cy="5" r="4" fill="none" stroke="var(--orange)" stroke-width="1.1"/><path d="M1 5h8M5 1c-2 2.5-2 5.5 0 8M5 1c2 2.5 2 5.5 0 8" fill="none" stroke="var(--orange)" stroke-width=".9"/></svg>
        <span>www.<span class="contact__web-domain">coralpennant.com</span></span>
      </li>
    </ul>
  </div>

  <svg class="edge-bands" viewBox="0 0 540 14" preserveAspectRatio="none" aria-hidden="true">
    <polygon points="0,7 318,7 310,14 0,14" fill="var(--blue)"/>
    <polygon points="326,0 540,0 540,14 314,14" fill="var(--orange)"/>
  </svg>
</section>

<section class="card card--brand">
  <div class="brand">
    <span class="brand__mark"></span>
    <span class="brand__name">Coral Pennant</span>
  </div>

  <svg class="edge-bands" viewBox="0 0 540 14" preserveAspectRatio="none" aria-hidden="true">
    <polygon points="0,7 318,7 310,14 0,14" fill="var(--blue)"/>
    <polygon points="326,0 540,0 540,14 314,14" fill="var(--orange)"/>
  </svg>
</section>

</body>
</html>
```